Ridgeline Journeys business card

please see website
www.ridgelinejourneys.comau

info needed on card
Curtis Halvey
Ph
email
Adventure Riding GPS trails

please use my logo and colours off my site

Curtis Halvey
curtis@ridgelinejourneys.com

```html
<!DOCTYPE html>
<html lang="en">
<head>
<meta charset="utf-8">
<title>Ridgeline Journeys business card</title>
<link rel="stylesheet" href="https://fonts.googleapis.com/css2?family=Open+Sans:ital,wght@0,400;0,600;0,700;1,700&display=swap">
<style>
  :root {
    --backdrop: #000000;
    --card: #ffffff;
    --ink: #1b1b1b;
    --rule: #9a9a9a;
    --mark: #636363;
  }
  * { margin: 0; padding: 0; box-sizing: border-box; }
  html, body { width: 1200px; height: 900px; overflow: hidden; background: var(--backdrop); }
  body { position: relative; font-family: "Open Sans", Arial, sans-serif; color: var(--ink); }

  .card { position: absolute; background: var(--card); width: 477px; height: 293px; }
  .card--front { left: 116px; top: 275px; border-radius: 0 46px 0 46px; }
  .card--back  { left: 622px; top: 276px; height: 292px; border-radius: 46px 0 46px 0; }

  .brand { position: absolute; display: flex; align-items: center; gap: 18px; }
  .brand__dot { width: 74px; height: 74px; border-radius: 50%; background: var(--mark); flex: none; }
  .brand__name { font-weight: 700; font-size: 31px; line-height: 1.08; color: var(--ink); }
  .card--front .brand { left: 92px; top: 36px; }
  .card--back .brand  { left: 96px; top: 92px; }

  .tagline {
    position: absolute; left: 0; right: 0; top: 137px; text-align: center;
    font-weight: 700; font-style: italic; font-size: 12.5px; letter-spacing: .2px;
    padding-left: 0;
  }

  .ruled { position: absolute; left: 0; right: 0; display: flex; align-items: center; gap: 6px; }
  .ruled::before, .ruled::after { content: ""; flex: 1; height: 1px; background: var(--rule); }
  .card--front .ruled { top: 182px; }
  .card--back .ruled  { top: 221px; }
  .holder { font-weight: 600; font-size: 15px; }
  .site   { font-weight: 600; font-size: 12px; }

  .contacts { position: absolute; left: 0; right: 0; top: 213px; list-style: none; text-align: center; font-size: 13px; line-height: 20px; }
  .contacts li { display: flex; justify-content: center; align-items: center; gap: 4px; }
  .contacts svg { width: 10px; height: 10px; fill: var(--ink); }
</style>
</head>
<body>
  <section class="card card--front">
    <div class="brand">
      <span class="brand__dot"></span>
      <span class="brand__name">Ridgeline<br>Journeys</span>
    </div>
    <p class="tagline">ADVENTURE RIDING GPS TRAILS</p>
    <div class="ruled"><span class="holder">Curtis Halvey</span></div>
    <ul class="contacts">
      <li><svg viewBox="0 0 10 10"><path d="M1 3c0-1 1-2 4-2s4 1 4 2v1H7V3H3v1H1zM2 5h6l1 4H1z"/></svg>(044)-512-3086</li>
      <li><svg viewBox="0 0 10 10"><path d="M0 2h10v6H0zM1 3v.4l4 2.6 4-2.6V3L5 5.4z" fill-rule="evenodd"/></svg>curtis@ridgelinejourneys.com</li>
      <li><svg viewBox="0 0 10 10"><path d="M6 1l3 3-2 2-1-1 1-1-1-1-3 3 1 1-1 1-1-1a1.4 1.4 0 0 1 0-2zM4 9L1 6l2-2 1 1-1 1 1 1 3-3-1-1 1-1 1 1a1.4 1.4 0 0 1 0 2z"/></svg>www.ridgelinejourneys.com</li>
    </ul>
  </section>

  <section class="card card--back">
    <div class="brand">
      <span class="brand__dot"></span>
      <span class="brand__name">Ridgeline<br>Journeys</span>
    </div>
    <div class="ruled"><span class="site">www.ridgelinejourneys.com</span></div>
  </section>
</body>
</html>
```